Hvac and insulation company needs good looking business card design

We are hvac and insulation company and looking for a new business cards that look to today standards designs

Target Market(s)

homeowners

Industry/Entity Type

Hvac

Contact Information for Business Card

Name: Walter Brinoku
Home comfort consultant
address: 4827 Dunmore St #215 Oakland, CA 94619
office: 888-316-2790
cell: 510-742-3185
Lic.# 584261
Email: walter@corvane-hvac.com
Web: corvane-hvac.com

Requirements
Must have
• clean and sleek look
Nice to have
• simple with a clean look
Should not have
• to busy business card

```html
<!DOCTYPE html>
<html lang="en">
<head>
<meta charset="utf-8">
<title>Corvane Home Solutions – Business Card</title>
<link rel="stylesheet" href="https://fonts.googleapis.com/css2?family=Arimo:wght@400;700&display=swap">
<style>
  :root {
    --backdrop: #4f4f4f;
    --card-light: #ffffff;
    --card-dark: #272727;
    --brand-orange: #f58220;
    --ink: #333333;
    --rule: #9a9a9a;
    --muted: #8a8a8a;
    --on-dark: #ffffff;
  }
  * { margin: 0; padding: 0; box-sizing: border-box; }
  html, body { width: 1200px; height: 900px; overflow: hidden; }
  body {
    background: var(--backdrop);
    font-family: "Arimo", Arial, sans-serif;
    position: relative;
  }
  .card {
    position: absolute;
    top: 306px;
    width: 440px;
    height: 271px;
    border-radius: 12px;
    box-shadow: 2px 4px 6px rgba(0,0,0,0.55);
  }
  .card--front { left: 149px; background: var(--card-light); }
  .card--back { left: 609px; background: var(--card-dark); }

  .front-brand {
    position: absolute;
    left: 36px;
    top: 112px;
    display: flex;
    align-items: center;
    gap: 10px;
    color: var(--brand-orange);
    font-weight: 700;
    font-size: 32px;
    letter-spacing: -0.5px;
  }
  .brand-square {
    width: 26px; height: 26px;
    background: var(--brand-orange);
    border-radius: 3px;
  }
  .divider {
    position: absolute;
    left: 215px;
    top: 54px;
    width: 1px;
    height: 160px;
    background: var(--rule);
  }
  .contact {
    position: absolute;
    left: 236px;
    top: 52px;
    color: var(--ink);
    font-size: 13px;
    line-height: 16px;
  }
  .contact__name {
    color: var(--brand-orange);
    font-weight: 700;
    font-size: 19px;
    line-height: 22px;
  }
  .contact__title { margin-bottom: 6px; }
  .contact__license { margin-bottom: 6px; }
  .contact__license .label { color: var(--brand-orange); }
  .contact__lines { list-style: none; margin-bottom: 6px; }
  .contact__lines li { display: flex; align-items: center; gap: 4px; }
  .contact__lines svg { width: 10px; height: 10px; fill: var(--brand-orange); flex: none; }

  .back-brand {
    position: absolute;
    left: 80px;
    top: 106px;
    display: flex;
    align-items: center;
    gap: 12px;
  }
  .back-brand .brand-square { width: 40px; height: 40px; border-radius: 4px; }
  .back-brand__name {
    color: var(--brand-orange);
    font-weight: 700;
    font-size: 42px;
    line-height: 40px;
    letter-spacing: -0.5px;
  }
  .back-brand__tagline {
    color: var(--muted);
    font-size: 15px;
    letter-spacing: 2px;
    margin-top: 2px;
    padding-left: 3px;
  }
  .back-web {
    position: absolute;
    left: 0; right: 0;
    top: 224px;
    text-align: center;
    color: var(--on-dark);
    font-size: 13px;
  }
</style>
</head>
<body>
  <section class="card card--front">
    <div class="front-brand"><span class="brand-square"></span><span>corvane</span></div>
    <div class="divider"></div>
    <div class="contact">
      <p class="contact__name">Walter Brinoku</p>
      <p class="contact__title">Home Comfort Consultant</p>
      <p class="contact__license"><span class="label">LIC.</span># 584261</p>
      <ul class="contact__lines">
        <li><svg viewBox="0 0 10 10"><path d="M1 3c0-1.5 1.5-2 4-2s4 .5 4 2v1H7V3H3v1H1z M2 5h6l1 4H1z"/></svg>888-316-2790</li>
        <li><svg viewBox="0 0 10 10"><path d="M3 0h4a1 1 0 0 1 1 1v8a1 1 0 0 1-1 1H3a1 1 0 0 1-1-1V1a1 1 0 0 1 1-1zm0 1.5v6h4v-6z"/></svg>510-742-3185</li>
        <li><svg viewBox="0 0 10 10"><path d="M0 2h10v1L5 6 0 3z M0 4l5 3 5-3v4H0z"/></svg>walter@corvane-hvac.com</li>
        <li><svg viewBox="0 0 10 10"><circle cx="5" cy="5" r="4.5"/></svg>www.corvane-hvac.com</li>
      </ul>
      <p>4827 Dunmore St</p>
      <p>#215 Oakland, CA 94619</p>
    </div>
  </section>

  <section class="card card--back">
    <div class="back-brand">
      <span class="brand-square"></span>
      <div>
        <p class="back-brand__name">corvane</p>
        <p class="back-brand__tagline">home solutions</p>
      </div>
    </div>
    <p class="back-web">www.corvane-hvac.com</p>
  </section>
</body>
</html>
```